NEW Wordpress Website Design for a Dynamic Long Term Healthcare Company in Hawaii

I would like a new website design for my current company, Marlow Health Collective, which has two different brands - Marlow Homecare and Marlow Senior Living. You can see the current website at www.marlowhealth-example.com. The website should be built using Wordpress Software and the Framewise theme. The website should have a local Hawaii island/tropical feel, but look professional for healthcare. I'm looking for something fresh, and want the designer to select colors, styles, etc.

In the Header, on all pages, I would like a menu that includes Home Care, Senior Living, Rates, and About Us.
Under each of the Header Menu Titles, I would like these drop downs included:
Home Care (drop down pages)- Nurse Aide Care, 24-Hour Home Care, Skilled Nursing, Lifestyle Aide, Hospice at Home, Bathing & Meal Service.
Senior Living (drop down pages) - Long-Term Stay, Short-Term Stay.
Rates (drop down page) - Rates.
About Us (drop down pages) - Our Mission, Ohana Talk, About Dana Marlow.

In the footer, on all pages, you should include the address: 248 Pueo Lane, Suite 310, Honolulu, HI 96817. Phone number: 808-555-0172
The footer should also include buttons for a page called Learn, Caregiver Jobs, and each of the service page links to include: Nurse Aide Care, 24-Hour Home Care, Skilled Nursing, Lifestyle Aide, Hospice at Home, Bathing & Meal Service.
Please don't take the current website and redesign a few aspects. I'm looking for a completely different look and feel.

Target Market(s)

40-80 year olds

Industry/Entity Type

Long Term Healthcare

Coding

Coded - Design and coding required

Requirements
Should not have
• Our existing website as a template. We are looking for a complete redesign. Thank you.

```html
<!DOCTYPE html>
<html lang="en">
<head>
<meta charset="utf-8">
<title>Marlow Health Collective</title>
<link href="https://fonts.googleapis.com/css2?family=Playfair+Display:wght@400;700&family=Lora:wght@400;500;600&display=swap" rel="stylesheet">
<style>
:root{
  --coral:#f07d71;
  --coral-deep:#d9675c;
  --coral-band:#e2685c;
  --coral-dark:#b04a42;
  --ink:#2b2b2b;
  --body:#4a4a4a;
  --teal:#3a8a8a;
  --night:#1e1f22;
  --footer:#1b1b1c;
  --white:#ffffff;
}
*{box-sizing:border-box;margin:0;padding:0}
html,body{width:1200px;height:5004px;overflow:hidden}
body{position:relative;background:var(--white);font-family:"Lora",serif;color:var(--body)}
.abs{position:absolute}
h1,h2,h3{font-family:"Playfair Display",serif;font-weight:400;color:var(--ink)}
.btn{position:absolute;display:flex;align-items:center;justify-content:center;border-radius:20px;background:var(--coral);color:var(--white);font-size:14px;height:34px;white-space:nowrap}
.para{font-size:13.5px;line-height:27px;color:var(--body)}
.eyebrow{font-size:15px;letter-spacing:1px;color:var(--teal);text-transform:uppercase}

/* top bar */
.topbar{top:0;left:0;width:1200px;height:31px;background:var(--coral-deep)}
.topbar .dot{position:absolute;top:7px;width:17px;height:17px;border-radius:50%;background:var(--white)}
.topbar .mail{position:absolute;left:782px;top:7px;color:var(--white);font-size:13px;display:flex;align-items:center;gap:8px}
.topbar .phoneblock{position:absolute;left:990px;top:0;width:210px;height:31px;background:#1f1f1f;clip-path:polygon(22px 0,100% 0,100% 100%,0 100%);display:flex;align-items:center;gap:8px;padding-left:28px;color:var(--white);font-size:13px}
.icon-circle{width:17px;height:17px;border-radius:50%;background:var(--white);display:flex;align-items:center;justify-content:center}

/* header */
.header{top:31px;left:0;width:1200px;height:101px;background:var(--white)}
.brand{position:absolute;left:60px;top:22px;display:flex;align-items:center;gap:10px}
.brand .mark{width:24px;height:24px;border-radius:50%;background:var(--coral)}
.brand .name{font-family:"Playfair Display",serif;font-size:22px;color:#6b6b6b;white-space:nowrap}
.nav{position:absolute;left:550px;top:41px;font-size:14px;color:var(--ink)}
.nav span{position:absolute;white-space:nowrap}
.nav .active{color:var(--coral)}
.contact-btn{left:1000px;top:35px;width:132px}

/* hero */
.hero-img{top:132px;left:0;width:1200px;height:560px;background:linear-gradient(135deg,#5a3a2c,#a07860 45%,#c9b49e)}
.hero-line{top:700px;left:0;width:1200px;height:5px;background:var(--coral)}
.hero-text{left:66px;top:276px;color:var(--white)}
.hero-text .kicker{font-family:"Playfair Display",serif;font-size:28px}
.hero-text .big{font-family:"Playfair Display",serif;font-size:56px;line-height:64px}
.hero-text .big b{font-weight:700}
.hero-text p{font-size:13px;line-height:27px;margin-top:12px;width:420px;color:var(--white)}

/* dropdown */
.dropdown{top:132px;left:188px;width:822px;height:392px;background:var(--white);box-shadow:0 6px 20px rgba(0,0,0,.12)}
.dropdown::before{content:"";position:absolute;left:398px;top:-14px;border:14px solid transparent;border-top:0;border-bottom-color:var(--white)}
.thumb{position:absolute;width:243px;height:120px;border-radius:4px}
.thumb-label{position:absolute;font-size:14px;color:var(--ink);text-decoration:underline}

/* photo frames */
.frame{position:absolute;width:470px;height:380px;border-radius:28px}

.about-text{left:649px;top:925px;width:490px}
.about-text h2{font-size:46px;line-height:52px;margin:14px 0 20px}

/* feature cards */
.feature{position:absolute;top:1486px;width:519px;height:374px;border-radius:34px;padding:50px 36px 0;color:var(--white)}
.feature h3{font-size:44px;line-height:54px;color:var(--white);margin-bottom:20px}
.feature p{font-size:13px;line-height:26.5px;color:var(--white)}
.feature .btn{left:36px;top:312px}
.feature.home{left:66px;background:linear-gradient(135deg,#8a4139,#a45a4f 60%,#c08172)}
.feature.living{left:614px;background:linear-gradient(135deg,#262626,#3c3a38 60%,#2a2a2a)}

.overview{left:70px;top:1995px;width:500px}
.overview h2{font-size:46px;line-height:58px;margin-bottom:22px}

/* pillars */
.pillars{top:2451px;left:0;width:1200px;height:689px;background:var(--night)}
.pillars .label{position:absolute;top:50px;width:1200px;text-align:center;color:var(--white);font-size:15px;letter-spacing:2px}
.pillars h2{position:absolute;top:78px;width:1200px;text-align:center;color:var(--white);font-size:46px}
.pillar{position:absolute;top:167px;width:250px;height:373px;background:var(--white);border-radius:22px;overflow:hidden}
.pillar .img{position:absolute;left:0;width:100%;height:160px}
.pillar .badge{position:absolute;left:100px;width:50px;height:50px;border-radius:50%;background:var(--coral);border:4px solid var(--white);display:flex;align-items:center;justify-content:center}
.pillar .body{position:absolute;left:16px;right:14px}
.pillar h3{font-size:20px;margin-bottom:12px}
.pillar p{font-size:12.5px;line-height:24px;color:var(--body)}
.pillar .more{font-size:11px;color:var(--teal);margin-top:8px;letter-spacing:.5px}

/* choice banner */
.choice{top:3082px;left:66px;width:1066px;height:299px;background:var(--coral-deep);border-radius:36px;text-align:center;color:var(--white)}
.choice .label{margin-top:46px;font-size:15px;letter-spacing:2px}
.choice h2{color:var(--white);font-size:46px;margin-top:6px}
.choice p{font-size:13px;line-height:27px;width:930px;margin:10px auto 0;color:var(--white)}
.choice .btn{position:relative;display:inline-flex;margin-top:20px;width:132px;background:var(--white);color:var(--ink)}

.living-text{left:651px;top:3520px;width:490px}
.living-text h2{font-size:46px;line-height:58px;margin-bottom:22px}

/* consultation */
.consult{top:3967px;left:0;width:1200px;height:540px;background:var(--coral-band)}
.consult-title{top:4015px;left:0;width:1200px;text-align:center;color:var(--white);font-size:46px;line-height:58px}
.field{position:absolute;height:43px;background:var(--white);font-size:12.5px;color:var(--ink);padding:0 16px;display:flex;align-items:center;justify-content:space-between}
.consent{top:4352px;left:0;width:1200px;text-align:center;font-size:11px;color:var(--white)}
.submit{left:520px;top:4381px;width:160px;height:41px;background:var(--coral-dark);letter-spacing:1px}

/* footer */
.footer-bg{top:4507px;left:0;width:1200px;height:497px;background:var(--footer)}
.footer-brand{left:66px;top:4641px;display:flex;align-items:center;gap:12px}
.footer-brand .mark{width:32px;height:32px;border-radius:50%;background:var(--white)}
.footer-brand .name{font-family:"Playfair Display",serif;font-size:26px;color:var(--white);white-space:nowrap}
.footer-tag{left:66px;top:4782px;width:300px;font-size:12px;line-height:25px;color:#d8d8d8}
.footer-head{position:absolute;top:4638px;font-family:"Playfair Display",serif;font-size:17px;color:var(--coral)}
.footer-list{position:absolute;top:4683px;list-style:none;font-size:12.5px;color:#e6e6e6;line-height:34px}
.contact-row{position:absolute;left:520px;display:flex;gap:14px;align-items:flex-start;font-size:12.5px;line-height:20px;color:#e6e6e6}
.contact-row .ico{width:28px;height:28px;border-radius:4px;background:var(--coral-deep);display:flex;align-items:center;justify-content:center;flex:none}
.rule{top:4932px;left:66px;width:1066px;height:1px;background:#3a3a3a}
.copyright{top:4958px;left:66px;font-size:11px;color:#cfcfcf}
.copyright span{color:var(--coral)}
.social{position:absolute;top:4960px;width:12px;height:12px;border-radius:50%;background:var(--coral)}
</style>
</head>
<body>

<div class="abs topbar">
  <span class="dot" style="left:66px"></span>
  <span class="dot" style="left:92px"></span>
  <span class="dot" style="left:118px"></span>
  <span class="dot" style="left:144px"></span>
  <div class="mail">
    <span class="icon-circle"><svg width="10" height="8" viewBox="0 0 10 8"><rect x=".5" y=".5" width="9" height="7" fill="none" stroke="#d9675c"/><path d="M.5 .5 5 4.5 9.5 .5" fill="none" stroke="#d9675c"/></svg></span>
    info@marlowhealth-example.com
  </div>
  <div class="phoneblock">
    <span class="icon-circle"><svg width="9" height="9" viewBox="0 0 10 10"><path d="M2 0 4 2.5 3 4c.8 1.5 1.6 2.3 3 3l1.5-1L10 8l-1.5 2C4 10 0 6 0 1.5Z" fill="#1f1f1f"/></svg></span>
    808-555-0172
  </div>
</div>

<header class="abs header">
  <div class="brand"><span class="mark"></span><span class="name">Marlow</span></div>
  <nav class="nav">
    <span class="active" style="left:0">Home Care ⌄</span>
    <span style="left:118px">Senior Living ⌄</span>
    <span style="left:252px">Rates ⌄</span>
    <span style="left:334px">About Us ⌄</span>
  </nav>
  <div class="btn contact-btn">Contact Us</div>
</header>

<div class="abs hero-img" role="img" aria-label="Caregiver helping a senior on a bed in a bright bedroom"></div>
<div class="abs hero-line"></div>

<div class="abs hero-text">
  <div class="kicker">Home Care</div>
  <div class="big"><b>Marlow</b></div>
  <div class="big">Services</div>
  <p>Homecare services that bring trusted, compassionate<br>care services provided in your own home.</p>
</div>
<div class="btn" style="left:66px;top:528px;width:134px">View Offer</div>

<div class="abs dropdown">
  <div class="thumb" role="img" aria-label="Smiling senior woman at home" style="left:31px;top:37px;background:linear-gradient(135deg,#d8c3ad,#9fb48a)"></div>
  <div class="thumb" role="img" aria-label="Caregiver walking with a senior outdoors" style="left:290px;top:37px;background:linear-gradient(135deg,#6d6d6d,#c8c8c8)"></div>
  <div class="thumb" role="img" aria-label="Nurse embracing a senior woman" style="left:550px;top:37px;background:linear-gradient(135deg,#5a5a5a,#d0d0d0)"></div>
  <div class="thumb-label" style="left:31px;top:166px;color:var(--coral)">Nurse Aide Care</div>
  <div class="thumb-label" style="left:290px;top:166px">24-Hour Home Care</div>
  <div class="thumb-label" style="left:550px;top:166px">Skilled Nursing</div>
  <div class="thumb" role="img" aria-label="Caregiver chatting with a senior" style="left:31px;top:208px;background:linear-gradient(135deg,#8a8a8a,#dcdcdc)"></div>
  <div class="thumb" role="img" aria-label="Senior resting on a sofa at home" style="left:290px;top:208px;background:linear-gradient(135deg,#cfcfcf,#8c8c8c)"></div>
  <div class="thumb" role="img" aria-label="Caregiver serving a meal in a kitchen" style="left:550px;top:208px;background:linear-gradient(135deg,#4a4a4a,#bdbdbd)"></div>
  <div class="thumb-label" style="left:31px;top:336px">Lifestyle Aide</div>
  <div class="thumb-label" style="left:290px;top:336px">Hospice at Home</div>
  <div class="thumb-label" style="left:550px;top:336px">Bathing &amp; Meal Service</div>
</div>

<div class="frame" role="img" aria-label="Nurse and senior woman smiling together on a couch" style="left:80px;top:900px;background:linear-gradient(135deg,#9a8b63,#4f88b6 55%,#b7c7a6)"></div>
<div class="abs about-text">
  <div class="eyebrow">About Us</div>
  <h2>Marlow Home Care<br>Group</h2>
  <p class="para">At Marlow Health Collective, our mission is to provide compassionate and professional long-term healthcare services that empower individuals to maintain their highest level of independence, health, and well-being in the comfort of their own homes or ours, either through our licensed home healthcare agency...</p>
</div>
<div class="btn" style="left:649px;top:1221px;width:133px">Read More</div>

<div class="feature home" role="img" aria-label="Caregiver with a senior in a warm home setting">
  <h3>Professional Care In<br>Your Home</h3>
  <p>Marlow Homecare understands that every person's care journey is unique. We tailor our in-home services to meet the diverse nurturing experience of professional quality care and safety within the comfort and convenience of your own home.</p>
  <div class="btn" style="width:212px">Schedule Care Assessment</div>
</div>
<div class="feature living" role="img" aria-label="Residents relaxing in a care home lounge">
  <h3>Trusted Care In Our<br>Home</h3>
  <p>Marlow Senior Living creates a warm, supportive, and enriching care home environment where seniors can thrive in their golden years. We provide residential care that promotes well-being, connection, and dignity of each individual.</p>
  <div class="btn" style="width:130px">Schedule Tour</div>
</div>

<div class="abs overview">
  <h2>Homecare<br>Services Overview</h2>
  <p class="para">Marlow Homecare is a leading provider of compassionate and professional homecare services. With a deep commitment to enhancing the quality of life for individuals of all ages, our company is dedicated to delivering personalized care in the comfort of our clients' homes.</p>
</div>
<div class="btn" style="left:70px;top:2255px;width:132px">Read More</div>
<div class="frame" role="img" aria-label="Caregiver serving breakfast to a senior couple at a dining table" style="left:650px;top:1955px;background:linear-gradient(135deg,#8a4a2e,#c9a27c 55%,#9fb07a)"></div>

<section class="abs pillars">
  <div class="label">SERVICES</div>
  <h2>Key Pillars of Our Mission</h2>

  <div class="pillar" style="left:66px">
    <div class="img" role="img" aria-label="Smiling senior woman" style="top:0;background:linear-gradient(135deg,#d8c3ad,#a7b58f)"></div>
    <div class="badge" style="top:135px"><svg width="20" height="20" viewBox="0 0 20 20"><path d="M8 2h4v6h6v4h-6v6H8v-6H2V8h6Z" fill="#fff"/></svg></div>
    <div class="body" style="top:200px"><h3>Nurse Aide Care</h3><p>Duis aute irure dolor in reprehenderit in voluptate velit esse cillum dolore eu fugiat nulla</p><div class="more">READ MORE</div></div>
  </div>

  <div class="pillar" style="left:342px">
    <div class="body" style="top:30px"><h3>24-Hour Home Care</h3><p>Duis aute irure dolor in reprehenderit in voluptate velit esse cillum dolore eu fugiat nulla</p><div class="more">READ MORE</div></div>
    <div class="img" role="img" aria-label="Caregiver walking with a senior on a garden path" style="top:213px;background:linear-gradient(135deg,#5f7a4a,#b9c7a0)"></div>
    <div class="badge" style="top:188px"><svg width="20" height="20" viewBox="0 0 20 20"><circle cx="10" cy="10" r="8" fill="none" stroke="#fff" stroke-width="2"/><path d="M10 5v5l3 2" fill="none" stroke="#fff" stroke-width="2"/></svg></div>
  </div>

  <div class="pillar" style="left:608px">
    <div class="img" role="img" aria-label="Nurse hugging a senior woman" style="top:0;background:linear-gradient(135deg,#7fa3c0,#e3d3c4)"></div>
    <div class="badge" style="top:135px"><svg width="20" height="20" viewBox="0 0 20 20"><path d="M8 2h4v6h6v4h-6v6H8v-6H2V8h6Z" fill="#fff"/></svg></div>
    <div class="body" style="top:200px"><h3>Skilled Nursing</h3><p>Duis aute irure dolor in reprehenderit in voluptate velit esse cillum dolore eu fugiat nulla</p><div class="more">READ MORE</div></div>
  </div>

  <div class="pillar" style="left:884px">
    <div class="body" style="top:30px"><h3>Lifestyle Aide</h3><p>Duis aute irure dolor in reprehenderit in voluptate velit esse cillum dolore eu fugiat nulla</p><div class="more">READ MORE</div></div>
    <div class="img" role="img" aria-label="Caregiver reading with a senior woman" style="top:213px;background:linear-gradient(135deg,#c7b6a3,#7c8fa4)"></div>
    <div class="badge" style="top:188px"><svg width="20" height="20" viewBox="0 0 20 20"><circle cx="10" cy="10" r="5" fill="#fff"/></svg></div>
  </div>
</section>

<section class="abs choice">
  <div class="label">HAWAII'S CHOICE</div>
  <h2>Homecare &amp; Senior Living</h2>
  <p>Marlow Homecare provides a variety of professional in-home health care services throughout the entire island of Oahu. Marlow Senior Living, a beautiful Adult Residential Care Home, is located on the windward side of Oahu in Kailua.</p>
  <div class="btn">More Info</div>
</section>

<div class="frame" role="img" aria-label="Three senior women knitting together in a sunny room" style="left:80px;top:3480px;background:linear-gradient(135deg,#c9b574,#b36a7a 55%,#d9cfae)"></div>
<div class="abs living-text">
  <h2>Marlow<br>Senior Living</h2>
  <p class="para">Choosing a senior living facility is crucial because it directly impacts the quality of life, well-being, and safety of seniors as they age. Marlow Senior Living offers a structured and supportive environment that addresses the unique needs and challenges that come with aging.</p>
</div>
<div class="btn" style="left:651px;top:3777px;width:132px">Read More</div>

<div class="abs consult"></div>
<h2 class="abs consult-title">Schedule a<br>Complimentary Care Consultation</h2>
<div class="field" style="left:188px;top:4183px;width:268px">Name:</div>
<div class="field" style="left:465px;top:4183px;width:270px">Email:</div>
<div class="field" style="left:742px;top:4183px;width:268px">Phone:</div>
<div class="field" style="left:188px;top:4239px;width:408px">How Can We Help? <span>⌄</span></div>
<div class="field" style="left:602px;top:4239px;width:408px">Question / Comments</div>
<div class="field" style="left:188px;top:4296px;width:408px">How did you hear About us?</div>
<div class="field" style="left:602px;top:4296px;width:408px">May we email you About this?</div>
<div class="abs consent">You agree to receive future emails and understand you may opt-out at any time</div>
<div class="btn submit">SUBMIT</div>

<div class="abs footer-bg"></div>
<div class="abs footer-brand"><span class="mark"></span><span class="name">Marlow</span></div>
<p class="abs footer-tag">Caregiving is a series of small acts of care that alter the course of someone's life.</p>
<div class="btn" style="left:66px;top:4849px;width:130px">Learn More</div>
<div class="btn" style="left:208px;top:4849px;width:132px;background:var(--white);color:var(--ink)">Caregiver Jobs</div>

<div class="footer-head" style="left:520px">Contact Us</div>
<div class="contact-row" style="top:4692px">
  <span class="ico"><svg width="12" height="14" viewBox="0 0 12 14"><path d="M6 14S0 8 0 5a6 6 0 0 1 12 0c0 3-6 9-6 9Z" fill="#fff"/><circle cx="6" cy="5" r="2" fill="#d9675c"/></svg></span>
  <span>248 Pueo Lane, Suite 310,<br>Honolulu, HI 96817</span>
</div>
<div class="contact-row" style="top:4758px">
  <span class="ico"><svg width="12" height="12" viewBox="0 0 10 10"><path d="M2 0 4 2.5 3 4c.8 1.5 1.6 2.3 3 3l1.5-1L10 8l-1.5 2C4 10 0 6 0 1.5Z" fill="#fff"/></svg></span>
  <span style="line-height:28px">808-555-0172</span>
</div>
<div class="contact-row" style="top:4816px">
  <span class="ico"><svg width="13" height="10" viewBox="0 0 10 8"><rect x=".5" y=".5" width="9" height="7" fill="none" stroke="#fff"/><path d="M.5 .5 5 4.5 9.5 .5" fill="none" stroke="#fff"/></svg></span>
  <span style="line-height:28px">hello@marlowhealth-example.com</span>
</div>

<div class="footer-head" style="left:812px">Quick Links</div>
<ul class="footer-list" style="left:812px">
  <li>Home Care</li><li>Senior Living</li><li>Rates</li><li>About Us</li><li>Contact Us</li>
</ul>

<div class="footer-head" style="left:1002px">Services</div>
<ul class="footer-list" style="left:1002px">
  <li>Nurse Aide Care</li><li>24-Hour Home Care</li><li>Skilled Nursing</li><li>Lifestyle Aide</li><li>Hospice at Home</li><li>Bathing &amp; Meal Service</li>
</ul>

<div class="abs rule"></div>
<div class="abs copyright">© <span>Marlow Health Collective</span>, 2024. All Rights Reserved</div>
<span class="social" style="left:1032px"></span>
<span class="social" style="left:1060px"></span>
<span class="social" style="left:1088px"></span>
<span class="social" style="left:1116px"></span>

</body>
</html>
```